Local Flower Farm Needs Business Card Design

I need business cards designed for a flower farm based in Eudora, Kansas.
Business Info:
We are a local cut flower farm located in Eudora, Kansas, founded by Corinne Haldwick. What started as a passion for agriculture and search for more joy in daily life has blossomed into a small business dedicated to providing the community with beautiful, fresh, and sustainable flowers. We specialize in local, seasonal blooms, ensuring that every petal reflects the care and dedication we pour into our craft. Our mission is to deliver the highest quality flowers directly to our customers through local farmers markets and to florists who share our commitment to sustainability. Join us in celebrating the beauty of nature, one bloom at a time!
Contact Details:
Corinne Haldwick
Owner
Phone 913-555-0147
Facebook: Rosalind Thorpe Gardens
Instagram: @RosalindThorpeGardens
Website: RosalindThorpeGardens.example
Target Market(s)
Wholesale to Florists and Direct to Consumer via Farmers Market
Industry/Entity Type
Florist, Farm
Contact Information for Business Card
Name, Contact Info, Logo
Look and feel
Each slider illustrates characteristics of the customer's brand and the style your logo design should communicate.

```html
<!DOCTYPE html>
<html lang="en">
<head>
<meta charset="utf-8">
<title>Rosalind Thorpe Gardens — Business Card</title>
<link rel="stylesheet" href="https://fonts.googleapis.com/css2?family=EB+Garamond:wght@400;500&display=swap">
<style>
  :root {
    --teal-deep: #0b2a31;
    --teal-soft: #12444e;
    --paper: #ffffff;
    --backdrop: #c9c9c9;
    --ink: #0b2a31;
  }
  * { box-sizing: border-box; margin: 0; padding: 0; }
  html, body { width: 1200px; height: 800px; overflow: hidden; }
  body {
    background: var(--backdrop);
    font-family: "EB Garamond", Georgia, serif;
    position: relative;
  }
  .card {
    position: absolute;
    left: 320px;
    width: 560px;
    height: 320px;
    border-radius: 22px;
    overflow: hidden;
    box-shadow: 0 10px 28px rgba(0,0,0,0.22);
  }
  .card--front { top: 50px; background: var(--paper); }
  .card--back { top: 430px; background: var(--teal-deep); }

  .band {
    position: absolute;
    left: 0; right: 0;
    top: 160px; height: 115px;
    background: var(--teal-deep);
  }
  .holder { position: absolute; left: 40px; top: 78px; color: var(--ink); }
  .holder__name {
    font-size: 23px; font-weight: 500;
    letter-spacing: 0.08em; text-transform: uppercase; line-height: 1;
  }
  .holder__role { font-size: 14px; margin-top: 4px; letter-spacing: 0.03em; }

  .contacts {
    position: absolute; left: 40px; top: 170px;
    list-style: none; color: var(--paper);
  }
  .contacts__item {
    display: flex; align-items: center; gap: 9px;
    height: 24px; font-size: 15px; letter-spacing: 0.01em;
  }
  .contacts__icon { width: 17px; height: 17px; flex: none; }

  .seal {
    position: absolute;
    width: 220px; height: 220px;
    border-radius: 50%;
    display: flex; align-items: center; justify-content: center;
    text-align: center;
  }
  .card--front .seal { left: 290px; top: 80px; background: var(--paper); }
  .seal__ring {
    position: absolute; inset: 12px;
    border-radius: 50%;
    border: 1.2px solid var(--ink);
  }
  .seal__name {
    font-size: 24px; font-weight: 500; line-height: 1.15;
    letter-spacing: 0.1em; text-transform: uppercase;
    color: var(--ink);
  }
  .card--back .seal { left: 170px; top: 50px; }
  .card--back .seal__ring { border-color: var(--teal-soft); inset: 0; }
  .card--back .seal__name { color: var(--teal-soft); }
</style>
</head>
<body>
  <section class="card card--front" aria-label="Business card front">
    <div class="band"></div>
    <div class="holder">
      <p class="holder__name">Corinne Haldwick</p>
      <p class="holder__role">Owner</p>
    </div>
    <ul class="contacts">
      <li class="contacts__item">
        <svg class="contacts__icon" viewBox="0 0 20 20" aria-hidden="true">
          <circle cx="10" cy="10" r="9" fill="none" stroke="#fff" stroke-width="1.2"/>
          <path d="M7 5.5c-.8.4-1.3 1.2-1 2.3.6 2.4 2.6 4.6 5 5.6 1.1.4 2 0 2.5-.8l-1.6-1.5-1.2.7c-1-.5-2-1.5-2.5-2.6l.8-1.1z" fill="#fff"/>
        </svg>
        913-555-0147
      </li>
      <li class="contacts__item">
        <svg class="contacts__icon" viewBox="0 0 20 20" aria-hidden="true">
          <circle cx="10" cy="10" r="9" fill="none" stroke="#fff" stroke-width="1.2"/>
        </svg>
        Rosalind Thorpe Gardens
      </li>
      <li class="contacts__item">
        <svg class="contacts__icon" viewBox="0 0 20 20" aria-hidden="true">
          <circle cx="10" cy="10" r="9" fill="none" stroke="#fff" stroke-width="1.2"/>
        </svg>
        @RosalindThorpeGardens
      </li>
      <li class="contacts__item">
        <svg class="contacts__icon" viewBox="0 0 20 20" aria-hidden="true">
          <circle cx="10" cy="10" r="9" fill="none" stroke="#fff" stroke-width="1.2"/>
          <circle cx="10" cy="10" r="5.5" fill="none" stroke="#fff" stroke-width="1"/>
          <ellipse cx="10" cy="10" rx="2.4" ry="5.5" fill="none" stroke="#fff" stroke-width="1"/>
          <path d="M4.5 10h11" stroke="#fff" stroke-width="1"/>
        </svg>
        RosalindThorpeGardens.example
      </li>
    </ul>
    <div class="seal">
      <span class="seal__ring"></span>
      <p class="seal__name">Rosalind<br>Thorpe<br>Gardens</p>
    </div>
  </section>

  <section class="card card--back" aria-label="Business card back">
    <div class="seal">
      <span class="seal__ring"></span>
      <p class="seal__name">Rosalind<br>Thorpe<br>Gardens</p>
    </div>
  </section>
</body>
</html>
```